Business Card Design

We are a company that provides stump grinding services for residential and commercial clients. Looking for a simple business card design that may have some type of graphic on the card that will tie in with the Tamsen name(Grizzly Bear, Paw Print, etc) . Possibly some foliage wrapping around part of the card? Would like to have a simple design that stands out because it is unique. We are working on getting the website set up and there is a simple graphic on the top of the page that came to mind when I mentioned the leaves.

Industry/Entity Type

Business

Contact Information for Business Card

Tamsen Stump Grinding 303-257-4788KodiakStumps.Com

Font styles to use
Serif

Requirements
Must have
• Business name
• Website Address
• Phone Number
Nice to have
• Graphics that would be associated with a Tamsen bear.
Should not have
• Nothing frilly

```html
<!DOCTYPE html>
<html lang="en">
<head>
<meta charset="utf-8">
<title>Tamsen Stump Grinding – Business Cards</title>
<link rel="stylesheet" href="https://fonts.googleapis.com/css2?family=Cinzel:wght@500&family=Open+Sans:wght@400&display=swap">
<style>
  :root {
    --backdrop: #e9e6e1;
    --card-black: #050505;
    --card-white: #ffffff;
    --ink-light: #f4f4f4;
    --ink-dark: #111111;
    --rule-light: #6a6a6a;
    --rule-dark: #9a9a9a;
    --shadow: rgba(0, 0, 0, 0.28);
  }
  * { box-sizing: border-box; margin: 0; padding: 0; }
  html, body {
    width: 1200px;
    height: 900px;
    overflow: hidden;
    background: var(--backdrop);
  }
  .canvas {
    position: relative;
    width: 1200px;
    height: 900px;
  }
  .card {
    position: absolute;
    width: 620px;
    height: 354px;
    box-shadow: 0 14px 30px var(--shadow);
    overflow: hidden;
  }
  .card--front {
    left: 110px;
    top: 110px;
    background: var(--card-black);
  }
  .card--back {
    left: 470px;
    top: 436px;
    background: var(--card-white);
  }
  .brand {
    position: absolute;
    display: flex;
    align-items: center;
    gap: 22px;
  }
  .card--front .brand { left: 50%; top: 50%; transform: translate(-50%, -50%); }
  .card--back .brand { left: 50%; top: 112px; transform: translate(-50%, -50%); }
  .brand__dot {
    width: 22px;
    height: 22px;
    border-radius: 50%;
  }
  .brand__divider {
    width: 1px;
    height: 66px;
  }
  .brand__name {
    font-family: "Cinzel", serif;
    font-weight: 500;
    line-height: 1.15;
  }
  .brand__line1 { display: block; font-size: 27px; letter-spacing: 0.02em; }
  .brand__line2 { display: block; font-size: 21px; letter-spacing: 0.62em; }
  .card--front .brand__dot { background: var(--ink-light); }
  .card--front .brand__divider { background: var(--rule-light); }
  .card--front .brand__name { color: var(--ink-light); }
  .card--back .brand__dot { background: var(--ink-dark); }
  .card--back .brand__divider { background: var(--rule-dark); }
  .card--back .brand__name { color: var(--ink-dark); }
  .contact-band {
    position: absolute;
    left: 0;
    right: 0;
    bottom: 0;
    height: 130px;
    background: var(--card-black);
  }
  .contact {
    position: absolute;
    display: flex;
    align-items: center;
    gap: 8px;
    font-family: "Open Sans", sans-serif;
    font-size: 17px;
  }
  .contact--web {
    right: 28px;
    top: 186px;
    color: var(--ink-dark);
    font-size: 15px;
  }
  .contact--phone {
    left: 30px;
    bottom: 38px;
    color: var(--ink-light);
  }
  .contact svg { flex: none; }
</style>
</head>
<body>
<main class="canvas">
  <section class="card card--front" aria-label="Card front">
    <div class="brand">
      <span class="brand__dot"></span>
      <span class="brand__divider"></span>
      <h1 class="brand__name">
        <span class="brand__line1">Tamsen Stump</span>
        <span class="brand__line2">Grinding</span>
      </h1>
    </div>
  </section>

  <section class="card card--back" aria-label="Card back">
    <div class="brand">
      <span class="brand__dot"></span>
      <span class="brand__divider"></span>
      <h2 class="brand__name">
        <span class="brand__line1">Tamsen Stump</span>
        <span class="brand__line2">Grinding</span>
      </h2>
    </div>

    <p class="contact contact--web">
      TamsenStumps.Com
      <svg width="12" height="12" viewBox="0 0 12 12" aria-hidden="true">
        <g fill="none" stroke="#111" stroke-width="1.3" stroke-linecap="round">
          <path d="M5 7 L7 5"/>
          <path d="M4.2 5.6 L2.6 7.2 a1.6 1.6 0 0 0 2.2 2.2 L6.4 7.8"/>
          <path d="M7.8 6.4 L9.4 4.8 a1.6 1.6 0 0 0 -2.2 -2.2 L5.6 4.2"/>
        </g>
      </svg>
    </p>

    <div class="contact-band">
      <p class="contact contact--phone">
        <svg width="16" height="14" viewBox="0 0 16 14" aria-hidden="true">
          <path fill="#f4f4f4" d="M1 4 C1 1.5 15 1.5 15 4 L15 5.5 L11.5 5.5 L11.5 4 L4.5 4 L4.5 5.5 L1 5.5 Z"/>
          <path fill="#f4f4f4" d="M4 6.5 L12 6.5 L14.5 12.5 L1.5 12.5 Z"/>
          <circle cx="8" cy="9.5" r="1.6" fill="#050505"/>
        </svg>
        303-555-0146
      </p>
    </div>
  </section>
</main>
</body>
</html>
```